Corvanth Veylor - Advanced Skincare and undetectable Makeup for Men

We are in need of a professional webpage for our company Corvanth Veylor. We help every man feel his best by looking his best. Inspired by the myth of Corvanth, we offer makeup and skincare products along with education upon their use. Our mission is to celebrate masculinity in all of its forms, regardless of age, race, sexual orientation, or assigned gender at birth.

The webpage would serve as our online store, as a place where our clients can learn about our brand, view our "How-to" video tutorials, and get product information. An online blog will also be hosted in order to keep clients up to date with news, updates, media mentions, etc.

The color schemes that we use are mostly Black and Gold, with Red accents. please keep in mind that this is a men's cosmetics line, and therefore should read powerful, sexy, confident and bold - all with a high end look and feel.

Think along the lines of brands like Lem Brisko, QDV, Belluti, etc.

our logo is included in the files attached. images and copy will be added in at a later time; hence, general images that fit the feel and filler text is encouraged.

The products to be sold include:
a face cleanser in a pump dispenser bottle (1 size)
a mask in a round jar container (1 size)
a moisturizer in a pump container 1 size)
a concealer in a click pen with a brush applicator (3 shades)
a liquid liner pen (4 shades)
a contouring palette (2 shade options)
a setting spray (single option)

Target Market(s)

Millennial Men

Industry/Entity Type

Beauty

Number of Pages Required

5+ page

Font styles to use
Serif

Colors
ec1f27
000000
faa54b

Requirements
Must have
• ur essential requirements are:
• 1) a stunning and engaging landing page that truly captures the ideals of sexuality, boldness and confidence.
• 2) an interactive and engaging online store that is easy to update / add product / information to.
• 3) Product pages supporting various toggling images of the product, a shade selection option, ingredient information, usage instructions, pricing, and a link to a "how to video" unique to each individual product.
• 4) dedicated space where all of the tutorials can be organized together
• 5) an organized Blog section, that would include a segment for a Q&A section for us to update as the brand grows, ongoing contests (that would be easily hidden if there are no contests running at the moment) as well as general news and updates segment.
• 6) an "about us" page, where our customers are able to learn about our story, inspirations, humanitarian efforts and philosophies in product contents and purity.
• 7) a contact us page, which would include social media links, contact email and telephone number as well as physical address to be updated upon launch.
• 8) discrete privacy policy, terms of use, and return policy links available at the bottom of every page
Nice to have
• 1) A posting forum where clients could post their looks using our products, or maybe a live stream of our Pictoval account.
• 2) a member sign in page so that we can collect and store customer information for faster check out, keep track of purchases attached to their email address (future loyalty program plans) and maintain an email database for email notifications and the such.

```html
<!DOCTYPE html>
<html lang="en">
<head>
<meta charset="utf-8">
<title>Corvanth Veylor – Skincare and Makeup for Men</title>
<link href="https://fonts.googleapis.com/css2?family=Montserrat:wght@400;600;700;800&family=Open+Sans:wght@400;600&family=Playfair+Display:ital,wght@1,600&family=Great+Vibes&family=Cinzel:wght@600&display=swap" rel="stylesheet">
<style>
:root{
  --gold:#b8893f;
  --gold-light:#d9b77a;
  --gold-pale:#efe3cc;
  --ink:#111111;
  --dark:#1c1c1c;
  --red:#e5232a;
  --text:#555555;
  --muted:#8a8a8a;
  --paper:#ffffff;
  --wall:#f1f0ee;
}
*{margin:0;padding:0;box-sizing:border-box}
html,body{width:1200px;height:4452px;overflow:hidden}
body{position:relative;background:var(--wall);font-family:"Open Sans",Arial,sans-serif;color:var(--text)}
.abs{position:absolute}
h2.section-title{position:absolute;left:0;width:1200px;text-align:center;font-family:Montserrat,Arial,sans-serif;font-weight:700;font-size:40px;color:var(--ink);letter-spacing:1px}
.btn{display:inline-block;font-family:Montserrat,Arial,sans-serif;font-weight:600;font-size:15px;color:#fff;background:var(--gold);border-radius:30px;padding:14px 30px;text-transform:uppercase;letter-spacing:.5px}
.btn-dark{background:#2a2a2a}

/* top bar */
.topbar{left:0;top:0;width:1200px;height:48px;background:#fff;border-bottom:1px solid #eee;font-size:14px;color:#444}
.topbar .item{position:absolute;top:14px;display:flex;align-items:center;gap:8px}
.topbar b{color:var(--gold);font-weight:600}

/* header */
.header{left:0;top:48px;width:1200px;height:152px;background:#fff}
.brand{position:absolute;display:flex;align-items:center;gap:12px}
.brand .mark{width:40px;height:40px;background:var(--gold)}
.brand .name{font-family:Cinzel,Georgia,serif;font-weight:600;color:var(--gold);font-size:22px;letter-spacing:2px}
.nav{position:absolute;left:390px;top:52px;display:flex;align-items:center;gap:14px;font-family:Montserrat,Arial,sans-serif;font-size:15px;font-weight:600;color:#333}
.nav a{padding:12px 22px;border-radius:24px;text-transform:uppercase}
.nav a.active{background:var(--gold);color:#fff}
.search{position:absolute;left:1072px;top:52px;width:46px;height:46px;border:2px solid #ccc;border-radius:50%;display:flex;align-items:center;justify-content:center}

/* hero */
.hero{left:0;top:200px;width:1200px;height:560px;background:linear-gradient(90deg,#0d0d0d 0%,#1e1b18 45%,#6b5a4c 75%,#2d2722 100%)}
.hero-photo{left:540px;top:200px;width:660px;height:560px;background:radial-gradient(ellipse at 55% 45%,#c9a58a 0%,#8c6c56 40%,rgba(40,32,28,0) 75%)}
.hero h1{left:80px;top:300px;font-family:Montserrat,Arial,sans-serif;font-weight:800;font-size:46px;color:#fff;letter-spacing:1px}
.hero p{left:80px;top:378px;width:440px;font-size:14px;line-height:22px;color:#e6e6e6}
.hero .btn{left:80px;top:506px;position:absolute}
.hero-curve{left:0;top:640px}

/* feature box */
.feature{left:160px;top:732px;width:880px;height:596px;background:#fff;box-shadow:0 10px 30px rgba(0,0,0,.15)}
.feature h3{position:absolute;left:28px;top:40px;font-family:Montserrat,Arial,sans-serif;font-weight:700;font-size:24px;line-height:30px;color:var(--ink);text-transform:uppercase}
.range-item{position:absolute;left:28px;width:470px;height:110px;border-bottom:1px solid #e6e6e6}
.range-item .thumb{position:absolute;left:0;top:14px;width:60px;height:80px;background:linear-gradient(#6e4a2a,#2c1d12);border-radius:4px}
.range-item .title{position:absolute;left:80px;top:10px;width:240px;font-family:"Playfair Display",Georgia,serif;font-style:italic;font-weight:600;font-size:19px;line-height:24px;color:var(--gold)}
.range-item .sub{position:absolute;left:80px;top:72px;font-size:12px;color:#666}
.range-item .price{position:absolute;left:390px;top:28px;width:96px;height:44px;border-radius:22px;background:var(--red);color:#fff;font-family:Montserrat,Arial,sans-serif;font-weight:600;font-size:17px;text-align:center;line-height:44px}
.promo{position:absolute;left:520px;top:0;width:360px;height:596px;background:linear-gradient(160deg,#c39a5a 0%,#a87c3c 55%,#8a6530 100%);text-align:center;color:#fff}
.promo .k1{margin-top:190px;font-family:Montserrat,Arial,sans-serif;font-size:16px;letter-spacing:2px}
.promo .k2{margin-top:8px;font-family:Montserrat,Arial,sans-serif;font-weight:600;font-size:34px;letter-spacing:3px}
.promo .k3{margin-top:6px;font-family:Montserrat,Arial,sans-serif;font-size:16px;letter-spacing:2px}
.promo .k4{margin-top:10px;font-family:"Great Vibes",cursive;font-size:56px;line-height:64px}
.promo .btn{margin-top:30px}

/* about */
.about-text{left:300px;top:1500px;width:600px;text-align:center;font-size:13px;line-height:22px}
.video{left:160px;top:1600px;width:880px;height:380px;background:linear-gradient(90deg,#3c3834 0%,#8a7d72 40%,#c4b8ab 60%,#5a524b 100%)}
.play{left:570px;top:1760px;width:60px;height:60px;border:3px solid #fff;border-radius:50%}
.about-btn{left:470px;top:2040px;position:absolute}

/* products */
.gold-band{left:0;top:2110px;width:1200px;height:280px;background:linear-gradient(180deg,var(--wall) 0%,var(--gold-pale) 35%,var(--gold-light) 100%)}
.card{position:absolute;background:#fff;box-shadow:0 6px 20px rgba(0,0,0,.12);text-align:center}
.card .pimg{margin:24px auto 0;width:120px;height:180px;border-radius:6px}
.card .cat{margin-top:22px;font-size:12px;color:#777;letter-spacing:1px}
.card .pname{margin-top:6px;font-family:Montserrat,Arial,sans-serif;font-weight:600;font-size:20px;color:var(--red)}
.card .stars{margin-top:4px;color:var(--gold);font-size:16px;letter-spacing:2px}
.card .stars span{color:#ccc}
.card .pprice{margin-top:6px;font-family:Montserrat,Arial,sans-serif;font-weight:700;font-size:26px;color:var(--ink)}
.card .actions{display:flex;justify-content:center;gap:8px;margin-top:14px}
.card .actions div{width:36px;height:36px;background:var(--gold);display:flex;align-items:center;justify-content:center}
.arrow{position:absolute;top:2866px;width:44px;height:44px;border-radius:50%;background:#fff;box-shadow:0 2px 8px rgba(0,0,0,.2);display:flex;align-items:center;justify-content:center}

/* testimonial */
.testimonial{left:160px;top:3060px;width:880px;height:300px;background:#fff;box-shadow:0 8px 24px rgba(0,0,0,.12);text-align:center}
.testimonial p{margin:120px auto 0;width:640px;font-family:"Playfair Display",Georgia,serif;font-style:italic;font-size:15px;line-height:24px;color:#777}
.testimonial .who{margin-top:16px;font-family:Montserrat,Arial,sans-serif;font-weight:600;font-size:14px;color:var(--gold);letter-spacing:1px}
.avatar{position:absolute;border-radius:50%;background:radial-gradient(circle at 50% 40%,#c7a88f,#4a3f38);border:4px solid #fff;box-shadow:0 2px 8px rgba(0,0,0,.2)}

/* news */
.news{position:absolute;top:3632px;width:320px;height:330px;overflow:hidden;box-shadow:0 4px 14px rgba(0,0,0,.1)}
.news .bg{position:absolute;inset:0}
.news .body{position:absolute;left:24px;top:22px;width:272px}
.news .label{font-family:"Playfair Display",Georgia,serif;font-style:italic;font-size:14px;color:#444}
.news h4{margin-top:12px;font-family:Montserrat,Arial,sans-serif;font-weight:600;font-size:20px;color:var(--gold)}
.news .date{margin-top:12px;font-size:13px;color:#555;display:flex;align-items:center;gap:8px}
.news p{margin-top:14px;font-size:13px;line-height:20px;color:#555}
.news .btn{position:absolute;left:24px;top:260px;background:#1c1c1c;font-size:13px;padding:11px 22px}
.news.dark .label,.news.dark p,.news.dark .date{color:#e8e8e8}

/* footer */
.footer{left:0;top:4000px;width:1200px;height:452px;background:#000;color:#ddd}
.footer h5{position:absolute;top:56px;font-family:Montserrat,Arial,sans-serif;font-weight:700;font-size:20px;color:#fff;letter-spacing:1px}
.links{position:absolute;top:104px;font-size:14px;line-height:26px}
.contact-row{position:absolute;left:800px;display:flex;gap:12px;font-size:13px;line-height:20px;color:#ccc}
.cards{position:absolute;left:800px;top:294px;display:flex;gap:8px}
.cards div{width:44px;height:28px;border-radius:3px;background:#d8d8d8}
.copyright{position:absolute;left:0;top:406px;width:1200px;text-align:center;font-size:13px;color:#bbb}
.copyright b{color:var(--gold)}
</style>
</head>
<body>

<!-- top bar -->
<div class="abs topbar">
  <div class="item" style="left:80px">
    <svg width="16" height="16" viewBox="0 0 24 24"><path d="M6.6 10.8a15 15 0 006.6 6.6l2.2-2.2c.3-.3.7-.4 1-.2 1.1.4 2.3.6 3.6.6.6 0 1 .4 1 1V20c0 .6-.4 1-1 1A17 17 0 013 4c0-.6.4-1 1-1h3.5c.6 0 1 .4 1 1 0 1.3.2 2.5.6 3.6.1.3 0 .7-.2 1z" fill="#333"/></svg>
    Call Us : <b>123-456-7890</b>
  </div>
  <div class="item" style="left:330px">
    <svg width="18" height="14" viewBox="0 0 24 18"><rect x="1" y="1" width="22" height="16" rx="2" fill="none" stroke="#333" stroke-width="2"/><path d="M1 2l11 8 11-8" fill="none" stroke="#333" stroke-width="2"/></svg>
    Mail Us : <b>admin@corvanthveylor.com</b>
  </div>
  <div class="item" style="left:880px">
    <svg width="18" height="16" viewBox="0 0 24 22"><path d="M1 2h4l3 12h12l3-9H7" fill="none" stroke="#333" stroke-width="2"/><circle cx="9" cy="19" r="2" fill="#333"/><circle cx="19" cy="19" r="2" fill="#333"/></svg>
    Cart &nbsp;|&nbsp; 0 items &nbsp;|&nbsp; $0.00
  </div>
</div>

<!-- header -->
<header class="abs header">
  <div class="brand" style="left:80px;top:52px">
    <div class="mark"></div>
    <div class="name">CORVANTH VEYLOR</div>
  </div>
  <nav class="nav">
    <a class="active">Home</a><a>About Us</a><a>Products</a><a>Blog</a><a>Contact</a>
  </nav>
  <div class="search">
    <svg width="18" height="18" viewBox="0 0 24 24"><circle cx="10" cy="10" r="7" fill="none" stroke="#777" stroke-width="2.5"/><path d="M15 15l7 7" stroke="#777" stroke-width="2.5"/></svg>
  </div>
</header>

<!-- hero -->
<section class="abs hero"></section>
<div class="abs hero-photo" role="img" aria-label="Photo of a confident man and a woman smiling, warm skin tones against a dark backdrop"></div>
<h1 class="abs hero" style="background:none;width:auto;height:auto;left:80px;top:300px">CORVANTH VEYLOR</h1>
<p class="abs" style="left:80px;top:378px;width:440px;font-size:14px;line-height:22px;color:#e6e6e6">Lorem ipsum is simply dummy text of the printing and typesetting industry. Lorem Ipsum has been the industry's standard dummy text ever since the 1500s, when an unknown printer took a galley of type and scrambled it.</p>
<a class="btn abs" style="left:80px;top:506px">Contact Us</a>
<svg class="abs hero-curve" width="1200" height="120" viewBox="0 0 1200 120"><path d="M0 120 Q600 30 1200 120 Z" fill="var(--wall)"/><path d="M0 118 Q600 28 1200 118" fill="none" stroke="var(--gold)" stroke-width="4"/></svg>

<!-- feature box -->
<section class="abs feature">
  <h3>Our Wide Range of<br>Products</h3>
  <div class="range-item" style="top:120px">
    <div class="thumb" role="img" aria-label="Face cleanser pump bottle"></div>
    <div class="title">A face cleanser in a pump dispenser bottle (1 size)</div>
    <div class="sub">20 mins Revitalise Facial</div>
    <div class="price">$ 30.00</div>
  </div>
  <div class="range-item" style="top:250px">
    <div class="thumb" role="img" aria-label="Moisturizer pump container"></div>
    <div class="title">A moisturizer in a pump container</div>
    <div class="sub">20 mins Revitalise Facial</div>
    <div class="price">$ 30.00</div>
  </div>
  <div class="range-item" style="top:380px;border-bottom:none">
    <div class="thumb" role="img" aria-label="Concealer click pen with brush applicator" style="background:linear-gradient(#3a3a3a,#111)"></div>
    <div class="title">A concealer in a click pen with a brush applicator</div>
    <div class="sub">20 mins Revitalise Facial</div>
    <div class="price">$ 30.00</div>
  </div>
  <div class="promo" role="img" aria-label="Warm golden photo of a bathroom vanity behind the offer">
    <div class="k1">COME</div>
    <div class="k2">EXPERIENCE</div>
    <div class="k3">THE REAL DELIGHT</div>
    <div class="k4">Glow Yourself</div>
    <a class="btn btn-dark">Buy Now</a>
  </div>
</section>

<!-- about -->
<h2 class="section-title" style="top:1428px">FEW WORD ABOUT US</h2>
<p class="abs about-text">Lorem ipsum is simply dummy text of the printing and typesetting industry. Lorem Ipsum has been the industry's standard dummy text ever since the 1500s, when an unknown printer took a galley of type and scrambled it. It is a type specimen book.</p>
<div class="abs video" role="img" aria-label="Video still of men applying skincare in front of a mirror"></div>
<svg class="abs" style="left:570px;top:1760px" width="60" height="60" viewBox="0 0 60 60"><circle cx="30" cy="30" r="27" fill="rgba(0,0,0,.25)" stroke="#fff" stroke-width="3"/><path d="M24 18l18 12-18 12z" fill="#fff"/></svg>
<a class="btn abs" style="left:468px;top:2040px">Watch a Video Now</a>

<!-- products -->
<div class="abs gold-band"></div>
<h2 class="section-title" style="top:2216px">OUR PRODUCTS</h2>

<div class="card" style="left:80px;top:2372px;width:240px;height:388px">
  <div class="pimg" role="img" aria-label="Liquid liner pens" style="background:linear-gradient(#f4eef6,#cdb2d8)"></div>
  <div class="cat">BRUSHES, LOTION</div><div class="pname">A setting spray</div>
  <div class="stars">★★★★<span>★</span></div><div class="pprice">$ 50.00</div>
</div>
<div class="card" style="left:348px;top:2320px;width:240px;height:492px">
  <div class="pimg" role="img" aria-label="Skincare set with bottles and jars" style="background:linear-gradient(#efe4d4,#b98a52);height:200px;width:150px"></div>
  <div class="cat">BRUSHES, LOTION</div><div class="pname">A setting spray</div>
  <div class="stars">★★★★<span>★</span></div><div class="pprice">$ 50.00</div>
  <div class="actions">
    <div><svg width="16" height="16" viewBox="0 0 24 22"><path d="M1 2h4l3 12h12l3-9H7" fill="none" stroke="#fff" stroke-width="2.5"/><circle cx="9" cy="19" r="2" fill="#fff"/><circle cx="19" cy="19" r="2" fill="#fff"/></svg></div>
    <div><svg width="16" height="16" viewBox="0 0 24 22"><path d="M12 21L3 12a5 5 0 017-7l2 2 2-2a5 5 0 017 7z" fill="#fff"/></svg></div>
    <div><svg width="18" height="14" viewBox="0 0 24 16"><path d="M1 8s4-7 11-7 11 7 11 7-4 7-11 7S1 8 1 8z" fill="none" stroke="#fff" stroke-width="2"/><circle cx="12" cy="8" r="3" fill="#fff"/></svg></div>
  </div>
</div>
<div class="card" style="left:612px;top:2372px;width:240px;height:388px">
  <div class="pimg" role="img" aria-label="Pump cleanser bottle" style="background:linear-gradient(#e8f6f8,#5bc3d3)"></div>
  <div class="cat">BRUSHES, LOTION</div><div class="pname">A setting spray</div>
  <div class="stars">★★★★<span>★</span></div><div class="pprice">$ 50.00</div>
</div>
<div class="card" style="left:880px;top:2372px;width:240px;height:388px">
  <div class="pimg" role="img" aria-label="Setting spray bottle" style="background:linear-gradient(#fbe6f1,#e14b9a)"></div>
  <div class="cat">BRUSHES, LOTION</div><div class="pname">A setting spray</div>
  <div class="stars">★★★★<span>★</span></div><div class="pprice">$ 50.00</div>
</div>
<div class="arrow" style="left:542px"><svg width="12" height="14" viewBox="0 0 12 14"><path d="M9 1L3 7l6 6" fill="none" stroke="#222" stroke-width="2.5"/></svg></div>
<div class="arrow" style="left:600px;background:#111"><svg width="12" height="14" viewBox="0 0 12 14"><path d="M3 1l6 6-6 6" fill="none" stroke="#fff" stroke-width="2.5"/></svg></div>

<!-- testimonial -->
<h2 class="section-title" style="top:2972px">CLIENT TESTIMONIAL</h2>
<section class="abs testimonial">
  <svg style="position:absolute;left:416px;top:42px" width="48" height="40" viewBox="0 0 48 40"><path d="M2 38V20C2 10 8 3 18 1l2 5c-6 2-9 6-9 12h9v20zM28 38V20c0-10 6-17 16-19l2 5c-6 2-9 6-9 12h9v20z" fill="var(--red)"/></svg>
  <p>Lorem ipsum is simply dummy text of the printing and typesetting industry. Lorem Ipsum has been the industry's standard dummy text ever since the 1500s, when an unknown printer took a galley of type and scrambled it. It is a type specimen book.</p>
  <div class="who">– ROWAN TASSEL –</div>
</section>
<div class="avatar" style="left:428px;top:3376px;width:80px;height:80px" role="img" aria-label="Client portrait"></div>
<div class="avatar" style="left:548px;top:3362px;width:104px;height:104px;border-color:var(--gold-light)" role="img" aria-label="Featured client portrait"></div>
<div class="avatar" style="left:692px;top:3376px;width:80px;height:80px" role="img" aria-label="Client portrait"></div>

<!-- news -->
<h2 class="section-title" style="top:3536px">LATEST NEWS</h2>
<article class="news" style="left:80px">
  <div class="bg" role="img" aria-label="Light photo of men's skin care products" style="background:linear-gradient(180deg,#f7f4ef,#e8e1d6)"></div>
  <div class="body">
    <div class="label">Collection</div><h4>2018 Men Skin Care Products</h4>
    <div class="date"><svg width="14" height="14" viewBox="0 0 24 24"><rect x="2" y="4" width="20" height="18" rx="2" fill="none" stroke="currentColor" stroke-width="2.5"/><path d="M2 10h20" stroke="currentColor" stroke-width="2.5"/></svg>8 August 2018</div>
    <p>Lorem Ipsum is simply dummy text of the printing and typesetting industry.</p>
  </div>
  <a class="btn">Read More</a>
</article>
<article class="news dark" style="left:432px">
  <div class="bg" role="img" aria-label="Dark photo of a man grooming" style="background:linear-gradient(180deg,#4b4540,#1f1c1a)"></div>
  <div class="body">
    <div class="label">Collection</div><h4>2018 Men Skin Care Products</h4>
    <div class="date"><svg width="14" height="14" viewBox="0 0 24 24"><rect x="2" y="4" width="20" height="18" rx="2" fill="none" stroke="currentColor" stroke-width="2.5"/><path d="M2 10h20" stroke="currentColor" stroke-width="2.5"/></svg>8 August 2018</div>
    <p>Lorem Ipsum is simply dummy text of the printing and typesetting industry.</p>
  </div>
  <a class="btn" style="background:var(--gold)">Read More</a>
</article>
<article class="news" style="left:788px">
  <div class="bg" role="img" aria-label="Light photo of a man's face care routine" style="background:linear-gradient(180deg,#f6f2ec,#e2d8ca)"></div>
  <div class="body">
    <div class="label">Collection</div><h4>2018 Men Skin Care Products</h4>
    <div class="date"><svg width="14" height="14" viewBox="0 0 24 24"><rect x="2" y="4" width="20" height="18" rx="2" fill="none" stroke="currentColor" stroke-width="2.5"/><path d="M2 10h20" stroke="currentColor" stroke-width="2.5"/></svg>8 August 2018</div>
    <p>Lorem Ipsum is simply dummy text of the printing and typesetting industry.</p>
  </div>
  <a class="btn">Read More</a>
</article>

<!-- footer -->
<footer class="abs footer">
  <div class="brand" style="left:120px;top:150px">
    <div class="mark"></div>
    <div class="name">CORVANTH VEYLOR</div>
  </div>
  <h5 style="left:436px">USEFUL LINKS</h5>
  <div class="links" style="left:436px">Home<br>About<br>Products<br>Blog<br>Contact</div>
  <div class="links" style="left:580px">Cart<br>Checkout<br>My account<br>Order Tracking<br>Privacy Policy</div>
  <h5 style="left:800px">CONTACT US</h5>
  <div class="contact-row" style="top:104px"><svg width="14" height="18" viewBox="0 0 24 30"><path d="M12 1a10 10 0 00-10 10c0 8 10 18 10 18s10-10 10-18A10 10 0 0012 1z" fill="var(--gold)"/><circle cx="12" cy="11" r="4" fill="#000"/></svg><span>123 Building Name, Street,<br>City, Country - Zip code</span></div>
  <div class="contact-row" style="top:166px"><svg width="16" height="16" viewBox="0 0 24 24"><path d="M6.6 10.8a15 15 0 006.6 6.6l2.2-2.2c.3-.3.7-.4 1-.2 1.1.4 2.3.6 3.6.6.6 0 1 .4 1 1V20c0 .6-.4 1-1 1A17 17 0 013 4c0-.6.4-1 1-1h3.5c.6 0 1 .4 1 1 0 1.3.2 2.5.6 3.6.1.3 0 .7-.2 1z" fill="var(--gold)"/></svg><span>+1 234 567 8900</span></div>
  <div class="contact-row" style="top:210px"><svg width="16" height="13" viewBox="0 0 24 18"><rect x="1" y="1" width="22" height="16" rx="2" fill="none" stroke="var(--gold)" stroke-width="2"/><path d="M1 2l11 8 11-8" fill="none" stroke="var(--gold)" stroke-width="2"/></svg><span>admin@corvanthveylor.com</span></div>
  <div class="cards"><div></div><div></div><div></div><div></div><div></div></div>
  <div class="copyright">Copyright © 2018 <b>CORVANTH VEYLOR</b>. All Rights Reserved.</div>
</footer>

</body>
</html>
```